Social media agency for startUps! Need captivating web banner(s) needed

We need a few banners if Possible for a lead generation - branding campaign we are about to launch on Workvine & Chatterloop. We are Social media Agency created to help Startup and small medium business build there digital footprint. We also offer a brand analysing service to help brands understand there real time impact along with consulting, coaching and managed services. We are very open to the design concept. We are looking for creativity and professionalism. Something that will captivate and peek interest in learning more about how a company can work with us. We are need banners for Chatterloop and Workvine. If you require the formats please ask and we will send them. 2 for each platform would be nice, but depending on cost we would be happy with i for each network.

Designs should have our tag line : Accelerated Marketing. Refreshing Results. it should alsl speak to the fact that we are the Social Media Agency for Startups in Canada.

Target Market(s)

Small Medium Business and Start up companies

Industry/Entity Type

Media

Requirements
Must have
• company name - TrailMOSS Social
• out tag line - Accelerated Marketing. Refreshing Results
• our Logo -
• ad size -
• 160x600 Workvine
• 30x250 Workvine
• 1,200 x 628 pixels Chatterloop
• Recommended image size: 600 x 600 pixels
Nice to have
• This is the hard part - I would like to see something like a collage of all the social networks and how our brand connects them to the business in question. The other aspect could be something related to when you leveled up in a video game.
• i know this is somewhat vague, but i am open to any question you might have relating to this project.

```html
<!DOCTYPE html>
<html lang="en">
<head>
<meta charset="utf-8">
<title>TrailMOSS Social – Canada's Social Media Agency for Startups</title>
<link rel="stylesheet" href="https://fonts.googleapis.com/css2?family=Oswald:wght@400;500&display=swap">
<style>
  :root {
    --navy: #262433;
    --orange: #f7931e;
    --white: #ffffff;
    --grey: #c8c8cc;
    --photo-base: #fbfaf6;
    --bubble-red: #ee6a45;
    --bubble-yellow: #f7e12c;
    --bubble-orange: #f6a623;
    --bubble-green: #b9d86c;
    --bubble-teal: #5ec3cf;
    --sleeve-blue: #3f6fa8;
  }
  html, body {
    margin: 0;
    padding: 0;
    overflow: hidden;
    background: var(--navy);
  }
  .banner {
    position: relative;
    width: 1200px;
    height: 1200px;
    overflow: hidden;
    background: var(--navy);
    font-family: "Oswald", "Arial Narrow", sans-serif;
  }
  .header {
    position: absolute;
    left: 0; top: 0;
    width: 1200px; height: 310px;
    background: var(--navy);
  }
  .brand {
    position: absolute;
    left: 110px; top: 40px;
    width: 380px;
    text-align: center;
  }
  .brand-mark {
    display: block;
    width: 130px; height: 130px;
    margin: 0 auto 20px;
    background: var(--orange);
  }
  .brand-name {
    display: block;
    color: var(--white);
    font-weight: 500;
    font-size: 40px;
    letter-spacing: 3px;
    line-height: 1;
    text-transform: uppercase;
    white-space: nowrap;
  }
  .brand-tagline {
    display: block;
    margin-top: 6px;
    color: var(--white);
    font-weight: 400;
    font-size: 19px;
    letter-spacing: 0.5px;
    line-height: 1.1;
    white-space: nowrap;
  }
  .headline {
    position: absolute;
    left: 562px; top: 81px;
    margin: 0;
    font-weight: 500;
    font-size: 55px;
    line-height: 90px;
    letter-spacing: 0.5px;
    text-transform: uppercase;
    white-space: nowrap;
  }
  .headline-accent { display: block; color: var(--orange); }
  .headline-main { display: block; color: var(--white); }
  .rule {
    position: absolute;
    left: 0; width: 1200px; height: 7px;
    background: var(--orange);
  }
  .rule-top { top: 310px; }
  .rule-bottom { top: 874px; }
  .hero-photo {
    position: absolute;
    left: 0; top: 317px;
    width: 1200px; height: 557px;
    background:
      radial-gradient(ellipse 170px 150px at 150px 330px, var(--bubble-red) 0%, rgba(238,106,69,0) 100%),
      radial-gradient(ellipse 210px 150px at 420px 190px, var(--bubble-yellow) 0%, rgba(247,225,44,0) 100%),
      radial-gradient(ellipse 190px 130px at 730px 110px, var(--bubble-orange) 0%, rgba(246,166,35,0) 100%),
      radial-gradient(ellipse 210px 150px at 600px 380px, var(--bubble-green) 0%, rgba(185,216,108,0) 100%),
      radial-gradient(ellipse 200px 150px at 1030px 320px, var(--bubble-teal) 0%, rgba(94,195,207,0) 100%),
      radial-gradient(ellipse 70px 110px at 800px 470px, var(--sleeve-blue) 0%, rgba(63,111,168,0) 100%),
      var(--photo-base);
  }
  .services {
    position: absolute;
    left: 0; top: 881px;
    width: 1200px; height: 319px;
    margin: 0; padding: 0;
    list-style: none;
  }
  .service {
    position: absolute;
    color: var(--grey);
    font-weight: 400;
    font-size: 46px;
    line-height: 1;
    letter-spacing: 1px;
    text-transform: uppercase;
    padding-left: 44px;
    white-space: nowrap;
  }
  .service::before {
    content: "";
    position: absolute;
    left: 0; top: 22px;
    width: 13px; height: 13px;
    border-radius: 50%;
    background: var(--grey);
  }
  .col-left { left: 74px; }
  .col-right { left: 570px; }
  .row-1 { top: 58px; }
  .row-2 { top: 132px; }
  .row-3 { top: 206px; }
</style>
</head>
<body>
<main class="banner" aria-label="TrailMOSS Social, Canada's social media agency for startups">
  <header class="header">
    <div class="brand">
      <span class="brand-mark"></span>
      <span class="brand-name">TrailMOSS Social</span>
      <span class="brand-tagline">Accelerated Marketing. Refreshing results</span>
    </div>
    <h1 class="headline">
      <span class="headline-accent">Accelerated Marketing.</span>
      <span class="headline-main">Refreshing Results</span>
    </h1>
  </header>

  <div class="rule rule-top"></div>

  <div class="hero-photo" role="img" aria-label="Photo of raised hands holding colourful speech bubbles reading share, news, chat, tweet and like, showing TrailMOSS Social as Canada's social media agency connecting startups to every network"></div>

  <div class="rule rule-bottom"></div>

  <ul class="services">
    <li class="service col-left row-1">Managed Services</li>
    <li class="service col-left row-2">Online Marketing</li>
    <li class="service col-left row-3">Social Media</li>
    <li class="service col-right row-1">Brand Analysing Service</li>
    <li class="service col-right row-2">Consulting</li>
    <li class="service col-right row-3">Coaching</li>
  </ul>
</main>
</body>
</html>
```